Mobile Repair Service on location needs a Web Design

We are starting a new mobile device repair service called Handset Haven and our website needs a design!

Hello Designers!
First, we'd like to make clear this is more than a simple web design contest, we want the designers to create an idea. We want someone who can create the whole theme of the service's we provide. We want someone that can help design our visual branding, help us communicate a sentiment. And we are willing to pay for that.

Who are we?
Our company is based in Rotterdam, the Netherlands. We provide different services for all kinds of electronic devices. The kind of services we provide are, among other things, installations of hardware and software and the repair of broken or malfunctioning devices.
We are starting a new service that offers mobile device repairs on location, be it at the home of our customers, their office, or any other place. Just give us the address and we will come to you for the repair job. This is also our main USP. We have multiple skilled engineers who drive trough the country on a daily basis and can be on location within a working day. Repair is done immediately onsite while the customer waits. At this stage we will start with the smartphone product-group within the mobile devices. In a second phase we might also add tablets.
People don't want to be without their phone for weeks because of some parts that needed to be ordered by a repair center they had to sent their phone to. We offer a fully functional mobile repair center in the form of specially customized vans. These vans have all the tools and utilities needed by our engineers to safely repair your mobile device. Your phone is being repaired directly in front of you, the next business-day, on a location you desire.

For this new service we are creating a website called Handset Haven. The website needs a story and matching design and this is where you come in. We are not looking for a simple template design we can get from any place. We need a story. We want you to create an idea, build a unique theme or vision that helps sell the product/service. This goes beyond the design of the website. We need the whole package, the design you are creating needs to have returning elements like icons, color use, images, maybe even characters etc. You name it! There needs to be a common thread in the design so we can reuse elements in, for example, the email templates, the work order or receipt we give to our customers (we may contact the winner of the contest to design these for us as well!).

The name 'Handset Haven' is chosen. Rehab (short for rehabilitate) has a bold and playful tone to it and the design needs to reflect the name. So we're looking for a somewhat playful and cheeky design. Definitely not too serious and definitely modern. We already got a logo that we love and that fit's this description (see attached design documents for the logo). It's bold, powerful and fun. Our web design needs to reflect this as well and has to fit in with our logo.
We would really like it if the design somehow incorporates elements that highlight our unique selling points (repairs on location, we come to you etc.). We would really like some form of story telling in the design. Think clumsy people breaking their phones. Teenagers in tears because they have no access to their friends. People nowadays have the need to always be 'connected'. What happens when your phone is broken or malfunctioning? We're handling tech, we are nerds and a little bit weird, but we're professionals and here to help you with your problem. The sentiment Byte Brigade tries to communicate is something we really like. We're looking for fresh idea's, anything goes!

In an overview all Unique Selling Points of the Handset haven service:
- Professional service on location. Don’t ship to us we will come to you!
- Clear pricing upfront. No hidden cost.
- Next business-day repair.
- Backed by a professional call center open 12 hours a day and open on a Saturday as well
- Backed by a professional repair center with more then 12 years of experience
- Repair is done by certified engineers
- 1 year warranty on the repair

The process:
The main function of our website will be for customers to make a repair request. A customer will visit our website and can make a repair request immediately by going through a 'request-order-flow'. In this flow he or she will need to fill in some forms and can select wich type/model/brand of mobile device he or she has and what parts need to be repaired. After a request is placed we will call the customer back (within an hour) for a short intake and to set a date/time and location. Our engineer will meet the customer at the specified location and will repair the device onsite in one of our mobile repair centers, which is a specialized van equipped with all the tools needed for device restorations.
So in short the steps are:
- Choose your device and repair job
- Place the order
- Get a callback within the hour
- Set date and location
- We will come to you.

Website functionality:
Our website is our main form of communication. So the sentiment we want to communicate needs be reflected in the design. We need a main/front page designed (preferably a long scrolling page design) containing:
1. Customers will be able to request a repair job directly on our website. So there will need to be a prominent button/link at the top of our main page that will bring the customer to this 'request-order-flow'. This is the main flow which needs to be full focus on the front page. All other items are secondary.
2. The general information of who we are and what we do, and why the customer should choose us. Preferably in short bullet-point type keywords/sentences with icons or other visual cues. See our unique selling points to get an idea of the information that will be displayed here.
3. There needs to be a section that will explain the process (see above) of a repair request step-by- step, again in brief short key sentences and with (custom) icons.
4. There needs to be a section that explains to the customer he/she can always contact us if they are not sure what the problem is with their device, and for this reason are not sure what repair request they should order.
5. We want to implement some functionality that display customer ratings or customer reviews. So there needs to be room for some kind of widget of plugin we're going to implement which shows these reviews.
6. A 'For business section' where we will explain all the options we provide for corporate clients.
7. Social media links.
8. There needs to be a menu with buttons that leads to the all sections described in the previous points.

For now, we need a design for our front page. In the second phase, when we have picked our winner, we may ask the winner to design the page(s) for our request workflow as well.

EDIT:
Finally, we have a very specific order in mind for the different segments of our website. We would like you to add some more segments that were not in our original brief as well:

1. Top header with order/request button. (should instantly make clear our main USP, we do repairs on location)
2. Our process
3. Our unique selling points / why choose us
4. The kind of repairs we do (broken screens, broken batteries, water damage, broken camera's, no sound etc.)
5. A 'meet our team' section, where we introduce some of our engineers
6. A 'contact us for any questions' section/
7. Testimonials/user reviews
8. A section where we show key performance indicators
9. 'For businesses' sections
10.'Subscribe for newsletter' field
11. Social media buttons

Industry/Entity Type

It Service

Number of Pages Required

1 page

Font styles to use
Sans Serif

Requirements
Must have
• a main/front page, design only
• custom icons/images for banners, adverts online and in print (high res)
Nice to have
• Storytelling in our design.
• Design that fits with our brand new logo.
• Elements like icons to have a flat design.
• Keep in mind that the website will need to be responsive when designing! (Ideally provide an example of the mobile design as well)
• Create a fun and trustworthy feeling.

```html
<!DOCTYPE html>
<html lang="en">
<head>
<meta charset="utf-8">
<title>Handset Haven – We Will Come to You</title>
<link rel="stylesheet" href="https://fonts.googleapis.com/css2?family=Raleway:wght@500;600;700;800&family=Open+Sans:wght@400;600;700&display=swap">
<style>
:root{
  --orange:#f26522;
  --orange-dark:#d9541a;
  --ink:#222;
  --text:#555;
  --muted:#888;
  --line:#e3e3e3;
  --grey-pin:#a9a9a9;
  --soft:#f4f4f4;
  --dark:#2b2b2b;
  --white:#fff;
}
*{box-sizing:border-box;margin:0;padding:0}
html,body{width:1200px;height:3711px;overflow:hidden}
body{font-family:'Open Sans',Arial,sans-serif;color:var(--text);background:var(--white);position:relative}
.head{font-family:'Raleway',Arial,sans-serif}
section,header,footer{position:absolute;left:0;width:1200px}
.abs{position:absolute}
.btn{position:absolute;background:var(--orange);color:var(--white);font-family:'Raleway',Arial,sans-serif;font-weight:700;font-size:13px;letter-spacing:.5px;text-transform:uppercase;display:flex;align-items:center;justify-content:center}

/* header */
.site-header{top:0;height:119px;background:var(--white)}
.topbar-call{position:absolute;top:0;left:625px;width:200px;height:35px;background:var(--dark);color:var(--white);font-size:12px;font-weight:700;display:flex;align-items:center;justify-content:center;clip-path:polygon(0 0,100% 0,93% 100%,7% 100%)}
.topbar-request{position:absolute;top:0;left:812px;width:228px;height:35px;background:var(--orange);color:var(--white);font-size:12px;font-weight:700;display:flex;align-items:center;justify-content:center;clip-path:polygon(0 0,100% 0,93% 100%,7% 100%)}
.brand{position:absolute;left:161px;top:34px;display:flex;align-items:center;gap:14px}
.brand-dot{width:54px;height:54px;border-radius:50%;background:var(--orange)}
.brand-name{font-family:'Raleway',Arial,sans-serif;font-weight:800;font-size:28px;line-height:28px;color:var(--ink);text-transform:uppercase;width:140px}
.main-nav{position:absolute;left:405px;top:72px;display:flex;gap:0;font-family:'Raleway',Arial,sans-serif;font-weight:700;font-size:12px;color:var(--ink)}
.main-nav span{padding:0 21px;text-transform:uppercase}
.main-nav .active{color:var(--orange)}
.header-rule{position:absolute;left:405px;top:112px;width:64px;height:3px;background:var(--orange)}

/* hero */
.hero{top:119px;height:514px;background:linear-gradient(100deg,#3c3e42 0%,#55585d 45%,#8b8d90 70%,#c9cacc 100%)}
.hero-visual{position:absolute;right:0;top:0;width:640px;height:514px;background:radial-gradient(ellipse at 60% 40%,rgba(255,255,255,.55),rgba(255,255,255,0) 60%)}
.hero h1{position:absolute;left:161px;top:160px;font-family:'Raleway',Arial,sans-serif;font-weight:700;font-size:42px;color:var(--white);text-transform:uppercase}
.hero h2{position:absolute;left:161px;top:215px;font-family:'Raleway',Arial,sans-serif;font-weight:700;font-size:19px;color:var(--white)}
.hero p{position:absolute;left:161px;top:253px;width:390px;font-size:12px;line-height:20px;color:#e6e6e6}
.hero .btn{left:161px;top:331px;width:94px;height:30px;font-size:11px}
.hero-arrow{position:absolute;top:240px}

/* process */
.process{top:633px;height:443px;background:var(--soft)}
.section-title{position:absolute;left:0;width:1200px;text-align:center;font-family:'Raleway',Arial,sans-serif;font-weight:700;font-size:25px;color:var(--ink)}
.section-title em{font-style:normal;color:var(--orange)}
.step{position:absolute;top:106px;width:200px;text-align:center}
.step svg{display:block;margin:0 auto}
.step p{margin-top:12px;font-size:14px;line-height:22px;color:#444}
.process-wave{position:absolute;left:60px;top:330px}

/* services */
.services{top:1076px;height:532px;background:var(--white)}
.usp{position:absolute;width:430px;height:80px;border:1px solid var(--line);display:flex;align-items:center;padding:0 48px 0 58px;font-size:14px;line-height:22px;color:#444}
.usp svg{position:absolute;left:18px;top:28px}
.usp .plus{position:absolute;right:18px;top:26px;color:#999;font-size:18px}

/* team photo */
.team-photo{top:1608px;height:416px;background:linear-gradient(100deg,#e9dccf 0%,#c7a38f 25%,#b6544a 45%,#d9cdc3 65%,#eeeeee 100%)}
.notch{position:absolute;left:580px;top:1998px;width:0;height:0;border-left:16px solid transparent;border-right:16px solid transparent;border-bottom:26px solid var(--white)}

/* about columns */
.about{top:2024px;height:289px}
.about-col{position:absolute;top:54px;width:270px}
.about-col h3{font-family:'Raleway',Arial,sans-serif;font-weight:700;font-size:17px;color:var(--ink)}
.about-col p{margin-top:18px;font-size:11px;line-height:20px;color:#666}
.about-col .btn{position:absolute;top:141px;left:0;width:92px;height:30px;font-size:10px}

/* testimonials */
.reviews{top:2313px;height:366px;background:linear-gradient(100deg,#2a2526 0%,#4a2f2c 40%,#6d3a32 70%,#3a2a2a 100%)}
.reviews h3{position:absolute;left:161px;top:110px;font-family:'Raleway',Arial,sans-serif;font-weight:700;font-size:25px;line-height:32px;color:var(--white)}
.dots{position:absolute;left:170px;top:228px;display:flex;gap:5px}
.dots i{width:11px;height:11px;border-radius:50%;background:#999;display:block}
.dots i:first-child{background:var(--white)}
.avatar-pin{position:absolute;left:445px;top:96px}
.quote{position:absolute;left:589px;top:116px;width:520px;font-size:12px;line-height:19px;font-style:italic;color:#ddd}
.quote b{font-style:normal;color:var(--orange);font-size:18px}
.author{position:absolute;left:589px;top:224px;font-size:12px;font-weight:700;color:var(--white)}

/* fix today */
.fix{top:2679px;height:611px;background:var(--white)}
.device{position:absolute;left:161px;top:87px;width:210px;height:418px;border-radius:28px;background:#1c1c1c}
.device-screen{position:absolute;left:14px;top:52px;width:182px;height:314px;background:linear-gradient(160deg,#5b5fa8,#b04e86 55%,#e08a6a)}
.fix h2{position:absolute;left:443px;top:70px;font-family:'Raleway',Arial,sans-serif;font-weight:700;font-size:27px;color:var(--ink)}
.fix h2 em{font-style:normal;color:var(--orange)}
.repair{position:absolute;width:300px}
.repair h4{font-family:'Raleway',Arial,sans-serif;font-weight:700;font-size:15px;color:var(--ink)}
.repair p{margin-top:12px;font-size:11px;line-height:19px;color:#666}
.fix .btn{left:443px;top:500px;width:146px;height:38px}

/* newsletter */
.newsletter{top:3290px;height:82px;background:var(--orange)}
.newsletter h3{position:absolute;left:161px;top:27px;font-family:'Raleway',Arial,sans-serif;font-weight:700;font-size:21px;color:var(--white);text-transform:uppercase}
.email{position:absolute;left:584px;top:21px;width:356px;height:40px;background:var(--white);font-size:13px;color:#777;padding-left:12px;display:flex;align-items:center}
.signup{position:absolute;left:945px;top:21px;width:94px;height:40px;background:var(--dark);color:var(--white);font-family:'Raleway',Arial,sans-serif;font-weight:700;font-size:13px;display:flex;align-items:center;justify-content:center}

/* footer */
.site-footer{top:3372px;height:339px;background:#f1f1f1}
.site-footer .brand{top:38px}
.footer-about{position:absolute;left:161px;top:138px;width:200px;font-size:12px;line-height:19px;color:#555}
.socials{position:absolute;left:161px;top:260px;display:flex;gap:7px}
.socials i{width:34px;height:34px;border-radius:50%;background:var(--orange);display:block}
.fcol{position:absolute;top:36px}
.fcol h5{font-family:'Raleway',Arial,sans-serif;font-weight:700;font-size:14px;color:var(--orange);text-transform:uppercase;margin-bottom:14px}
.fcol li{list-style:none;font-size:11px;line-height:23px;color:#555}
.footer-rule{position:absolute;left:430px;top:270px;width:610px;height:1px;background:#ddd}
.copyright{position:absolute;left:768px;top:285px;font-size:11px;color:#555}
</style>
</head>
<body>

<header class="site-header">
  <div class="topbar-call">CALL US: 555-010-2040</div>
  <div class="topbar-request">REQUEST-ORDER-FLOW</div>
  <div class="brand"><span class="brand-dot"></span><span class="brand-name">Handset Haven</span></div>
  <nav class="main-nav">
    <span class="active">Home</span><span>Services</span><span>Products</span><span>About</span><span>Gallery</span><span>Blog</span><span>Contact</span>
    <span><svg width="13" height="13" viewBox="0 0 13 13"><circle cx="5.5" cy="5.5" r="4" fill="none" stroke="#222" stroke-width="1.8"/><line x1="8.5" y1="8.5" x2="12" y2="12" stroke="#222" stroke-width="1.8"/></svg></span>
  </nav>
  <div class="header-rule"></div>
</header>

<section class="hero">
  <div class="hero-visual" role="img" aria-label="Cracked smartphone lying on a dark leather desk beside earphones and a pen"></div>
  <svg class="hero-arrow" style="left:56px" width="20" height="34" viewBox="0 0 20 34"><polyline points="17,2 3,17 17,32" fill="none" stroke="#fff" stroke-width="2"/></svg>
  <svg class="hero-arrow" style="left:1124px" width="20" height="34" viewBox="0 0 20 34"><polyline points="3,2 17,17 3,32" fill="none" stroke="#fff" stroke-width="2"/></svg>
  <h1>Handset Haven</h1>
  <h2>We Will Come to You!</h2>
  <p>Cracked screen, dead battery or a phone that took a swim? Our engineers drive to your home or office and fix it on the spot while you wait.</p>
  <div class="btn">Read More</div>
</section>

<section class="process">
  <h2 class="section-title" style="top:50px">Our <em>Handset Haven</em> Process</h2>
  <svg class="abs" style="left:290px;top:154px" width="640" height="6"><line x1="0" y1="3" x2="640" y2="3" stroke="#bbb" stroke-width="2" stroke-dasharray="2 7" stroke-linecap="round"/></svg>
  <svg class="abs" style="left:322px;top:150px" width="560" height="12"><g fill="#fff" stroke="#bbb" stroke-width="2"><circle cx="6" cy="6" r="4"/><circle cx="188" cy="6" r="4"/><circle cx="368" cy="6" r="4"/><circle cx="546" cy="6" r="4"/></g></svg>

  <div class="step" style="left:142px">
    <svg width="96" height="136" viewBox="0 0 96 136"><path d="M48 2a46 46 0 0 1 46 46c0 30-34 58-46 86C36 106 2 78 2 48A46 46 0 0 1 48 2z" fill="#f26522"/><circle cx="48" cy="48" r="36" fill="#fff"/><rect x="37" y="28" width="22" height="38" rx="3" fill="none" stroke="#f26522" stroke-width="3"/><circle cx="48" cy="60" r="2" fill="#f26522"/></svg>
    <p>Choose your device<br>and repair job</p>
  </div>
  <div class="step" style="left:328px">
    <svg width="96" height="136" viewBox="0 0 96 136"><path d="M48 2a46 46 0 0 1 46 46c0 30-34 58-46 86C36 106 2 78 2 48A46 46 0 0 1 48 2z" fill="#a9a9a9"/><circle cx="48" cy="48" r="36" fill="#fff"/><path d="M28 32h7l5 22h20l5-15H38" fill="none" stroke="#f26522" stroke-width="3" stroke-linejoin="round"/><circle cx="42" cy="61" r="3" fill="#f26522"/><circle cx="58" cy="61" r="3" fill="#f26522"/></svg>
    <p>Place the order</p>
  </div>
  <div class="step" style="left:509px">
    <svg width="96" height="136" viewBox="0 0 96 136"><path d="M48 2a46 46 0 0 1 46 46c0 30-34 58-46 86C36 106 2 78 2 48A46 46 0 0 1 48 2z" fill="#a9a9a9"/><circle cx="48" cy="48" r="36" fill="#fff"/><path d="M62 58c-4 4-8 4-12 2-6-3-11-8-14-14-2-4-2-8 2-12l4 6-3 4c2 4 5 7 9 9l4-3z" fill="#f26522"/></svg>
    <p>Get a callback<br>within the hour</p>
  </div>
  <div class="step" style="left:687px">
    <svg width="96" height="136" viewBox="0 0 96 136"><path d="M48 2a46 46 0 0 1 46 46c0 30-34 58-46 86C36 106 2 78 2 48A46 46 0 0 1 48 2z" fill="#a9a9a9"/><circle cx="48" cy="48" r="36" fill="#fff"/><path d="M48 28a12 12 0 0 1 12 12c0 9-12 22-12 22S36 49 36 40a12 12 0 0 1 12-12z" fill="#f26522"/><circle cx="48" cy="40" r="4" fill="#fff"/></svg>
    <p>Set date<br>and location</p>
  </div>
  <div class="step" style="left:867px">
    <svg width="96" height="136" viewBox="0 0 96 136"><path d="M48 2a46 46 0 0 1 46 46c0 30-34 58-46 86C36 106 2 78 2 48A46 46 0 0 1 48 2z" fill="#a9a9a9"/><circle cx="48" cy="48" r="36" fill="#fff"/><path d="M26 36h28v22H26zM54 42h10l6 8v8H54z" fill="#f26522"/><circle cx="35" cy="60" r="4" fill="#f26522" stroke="#fff" stroke-width="2"/><circle cx="62" cy="60" r="4" fill="#f26522" stroke="#fff" stroke-width="2"/></svg>
    <p>We will<br>come to you</p>
  </div>

  <svg class="process-wave" width="1080" height="60" viewBox="0 0 1080 60"><path d="M0 40C120 40 160 30 227 27S420 25 534 27s200 6 306 2 180 8 240 12" fill="none" stroke="#ccc" stroke-width="2"/><g fill="#fff" stroke="#f26522" stroke-width="2"><circle cx="227" cy="27" r="6"/><circle cx="534" cy="27" r="6"/><circle cx="840" cy="28" r="6"/></g></svg>
</section>

<section class="services">
  <h2 class="section-title" style="top:48px">Our <em>Handset Haven</em> Services</h2>
  <div class="usp" style="left:161px;top:119px"><svg width="18" height="24" viewBox="0 0 18 24"><path d="M9 0a9 9 0 0 1 9 9c0 7-9 15-9 15S0 16 0 9a9 9 0 0 1 9-9z" fill="#f26522"/><circle cx="9" cy="9" r="3" fill="#fff"/></svg>Professional service on location.<br>Don’t ship to us we will come to you!<span class="plus">+</span></div>
  <div class="usp" style="left:609px;top:119px"><svg width="22" height="22" viewBox="0 0 22 22"><circle cx="11" cy="11" r="10" fill="#f26522"/><path d="M11 5v6h5" fill="none" stroke="#fff" stroke-width="2"/></svg>Backed by a professional call center open 12 hours a day and open on a Saturday as well<span class="plus">+</span></div>
  <div class="usp" style="left:161px;top:208px"><svg width="24" height="22" viewBox="0 0 24 22"><path d="M0 2v8l12 12 10-10L10 0H2z" fill="#f26522"/><circle cx="6" cy="6" r="2" fill="#fff"/></svg>Clear pricing upfront. No hidden cost.<span class="plus">+</span></div>
  <div class="usp" style="left:609px;top:208px"><svg width="22" height="22" viewBox="0 0 22 22"><rect x="1" y="3" width="20" height="18" rx="2" fill="#f26522"/><rect x="3" y="8" width="16" height="11" fill="#fff"/><rect x="5" y="0" width="3" height="6" fill="#f26522"/><rect x="14" y="0" width="3" height="6" fill="#f26522"/></svg>Backed by a professional repair center with more then 12 years of experience<span class="plus">+</span></div>
  <div class="usp" style="left:161px;top:296px"><svg width="24" height="22" viewBox="0 0 24 22"><rect x="0" y="5" width="24" height="17" rx="2" fill="#f26522"/><rect x="8" y="1" width="8" height="6" rx="1" fill="none" stroke="#f26522" stroke-width="2"/></svg>Next business-day repair.<span class="plus">+</span></div>
  <div class="usp" style="left:609px;top:296px"><svg width="22" height="22" viewBox="0 0 22 22"><circle cx="11" cy="6" r="5" fill="#f26522"/><path d="M1 22c0-7 4-10 10-10s10 3 10 10z" fill="#f26522"/></svg>Repair is done by certified engineers<span class="plus">+</span></div>
  <div class="usp" style="left:161px;top:384px"><svg width="22" height="22" viewBox="0 0 22 22"><path d="M5 1h12v7a6 6 0 0 1-12 0zM9 14h4v4h3v3H6v-3h3z" fill="#f26522"/><path d="M5 3H1v3a4 4 0 0 0 4 4M17 3h4v3a4 4 0 0 1-4 4" fill="none" stroke="#f26522" stroke-width="2"/></svg>1 year warranty on the repair<span class="plus">+</span></div>
</section>

<section class="team-photo" role="img" aria-label="Friendly call center staff with headsets working at computers"></section>
<div class="notch"></div>

<section class="about">
  <div class="about-col" style="left:161px">
    <h3>Handset Haven &amp; Value Mart</h3>
    <p>Find us in selected stores across the country, or book online and let our mobile van come to your door the next business day.</p>
    <div class="btn">Read More</div>
  </div>
  <div class="about-col" style="left:476px">
    <h3>Expert Repair</h3>
    <p>Certified engineers repair your device right in front of you, using quality parts and the right tools in our fully equipped vans.</p>
    <div class="btn">Read More</div>
  </div>
  <div class="about-col" style="left:791px">
    <h3>Who Are We?</h3>
    <p>Our company is based in Rotterdam, the Netherlands. We provide different services for all kinds of electronic devices. The kind of services we provide are, among other things, installations...</p>
    <div class="btn">Read More</div>
  </div>
</section>

<section class="reviews" role="img" aria-label="Blurred photo of hands holding a smartphone in warm light">
  <h3>What Our<br>Customers Says</h3>
  <div class="dots"><i></i><i></i><i></i><i></i></div>
  <svg class="avatar-pin" width="120" height="200" viewBox="0 0 120 200"><path d="M60 2a58 58 0 0 1 58 58c0 40-40 70-58 138C42 130 2 100 2 60A58 58 0 0 1 60 2z" fill="#f26522"/><circle cx="60" cy="60" r="50" fill="#fff"/><circle cx="60" cy="60" r="45" fill="#9a8a80"/></svg>
  <p class="quote"><b>❝</b> I dropped my phone on the way to work and had it back in one piece before lunch. The engineer came to my office, explained everything and the price was exactly what was quoted. Quick, friendly and no fuss at all. <b>❞</b></p>
  <div class="author">Head of Fulfilment, City Name</div>
</section>

<section class="fix">
  <div class="device"><div class="device-screen" role="img" aria-label="Smartphone home screen with app icons"></div></div>
  <h2>What would you like to <em>fix today?</em></h2>
  <div class="repair" style="left:443px;top:133px"><h4>Cracked Screen</h4><p>New glass and display fitted onsite, so your screen looks and works like new again.</p></div>
  <div class="repair" style="left:772px;top:133px"><h4>Water Damage</h4><p>We dry, clean and test every part to bring your soaked phone back to life.</p></div>
  <div class="repair" style="left:443px;top:259px"><h4>Broken Buttons</h4><p>Stuck or loose buttons replaced quickly so every press works the way it should.</p></div>
  <div class="repair" style="left:772px;top:259px"><h4>Dead Battery</h4><p>A fresh battery fitted in minutes so your phone lasts through the whole day.</p></div>
  <div class="repair" style="left:443px;top:385px"><h4>Signal Problem</h4><p>Dropped calls or no bars? We check antennas and parts to restore your connection.</p></div>
  <div class="repair" style="left:772px;top:385px"><h4>Sound Problem</h4><p>No ring, no voice or crackling speakers fixed onsite with tested replacement parts.</p></div>
  <div class="btn">Get Started</div>
</section>

<section class="newsletter">
  <h3>Get Tax Coupons &amp; The Latest Deals</h3>
  <div class="email">Email Address</div>
  <div class="signup">SIGN UP</div>
</section>

<footer class="site-footer">
  <div class="brand"><span class="brand-dot"></span><span class="brand-name">Handset Haven</span></div>
  <p class="footer-about">Our company is based in Rotterdam, the Netherlands. We provide different services for all kinds of electronic devices.</p>
  <div class="socials"><i></i><i></i><i></i><i></i><i></i></div>
  <div class="fcol" style="left:430px"><h5>Site Map</h5><ul><li>Blog</li><li>Find A Store</li><li>Franchise Information</li><li>Locations</li><li>Buy / Sell / Trade</li></ul></div>
  <div class="fcol" style="left:609px"><h5>Services</h5><ul><li>Smartphone Repair</li><li>Computer Repair</li><li>Pear Phone Repair</li><li>Slate / Tablet Repair</li><li>Notebook Repair</li><li>Game System Repair</li></ul></div>
  <div class="fcol" style="left:806px"><h5>What We Do</h5><ul><li>Learning Centre</li><li>Services</li><li>Star Reviews</li><li>Portfolio</li><li>Reviews</li><li>Contact Us</li></ul></div>
  <div class="fcol" style="left:977px"><h5>Links</h5><ul><li>Home</li><li>Products</li><li>About</li><li>Services</li><li>Gallery</li><li>Blog</li></ul></div>
  <div class="footer-rule"></div>
  <div class="copyright">Copyright © 2017 Handset Haven.All Copyrights reserved</div>
</footer>

</body>
</html>
```